Norvane Website Design (New Start Up Investment Management Firm)

We need a website designed. We have attached a Powerpoint with our proposed website content (which is quite minimal), the format is just a suggestion but we would like to see your alternative and improved ideas. We are a boutique investment firm so are looking for something sleek and professional. I have included on the last page of the attachment our brand colours and font styles as well as attaching our logo design. We would like the successful designer to design the website and build the buttons etc.

On the "Contact Us" page, we are open to suggestions on how best to show the map, whether is should be static or open a google maps page. We would like the phone number and email address to be set up so people can click on them on their phone and it calls us or emails us directly.

We would prefer not to have photos of landscapes on the site.
Our website is hosted on a Linux based website.

We would also like 3 links at the bottom of each page for links to pdfs:
- Disclaimer, Terms and Conditions of Web Site Use
- Stewardship
- Pillar III

Target Market(s)

Institutional Investors

Industry/Entity Type

Investment

Coding

Coded - Design and coding required

Number of Pages Required

3 page

Font styles to use
Other font styles liked:
• Logo: Lato, Text: Source Sans Pro

Colors

Designer to choose colors to be used in the design.

Requirements
Must have
• The website must use the colours and fonts on the last page of the attached powerpoint. I can't see an option to select the exact colour palette below so please look at the PPT.
• For others please see Project description.
Should not have
• Landscape photos

```html
<!DOCTYPE html>
<html lang="en">
<head>
<meta charset="utf-8">
<title>Norvane Investment Management</title>
<link rel="stylesheet" href="https://fonts.googleapis.com/css2?family=Lato:wght@400;700;900&family=Source+Sans+3:wght@400;600&display=swap">
<style>
  :root {
    --navy: #002b5f;
    --royal: #1a44b0;
    --nav-grey: #555a60;
    --body-grey: #4a4d52;
    --rule: #e3e5e8;
    --copy-blue: #3f7fdc;
    --white: #ffffff;
  }
  * { box-sizing: border-box; margin: 0; padding: 0; }
  html, body { width: 1200px; height: 666px; overflow: hidden; background: var(--white); }
  body { font-family: "Source Sans 3", "Source Sans Pro", sans-serif; position: relative; }

  .site-header {
    height: 91px; border-bottom: 1px solid var(--rule);
    display: flex; align-items: center; justify-content: space-between;
    padding: 0 74px 0 76px;
  }
  .brand { display: flex; align-items: center; gap: 12px; text-decoration: none; }
  .brand-square { width: 54px; height: 54px; background: var(--navy); }
  .brand-name { font-family: "Lato", sans-serif; font-weight: 700; font-size: 44px; color: var(--navy); letter-spacing: 1px; }

  .main-nav { display: flex; gap: 0; }
  .main-nav a {
    font-family: "Lato", sans-serif; font-weight: 700; font-size: 15.5px;
    color: var(--nav-grey); text-decoration: none; text-transform: uppercase;
    padding: 10px 11px 10px; margin-left: 35px; position: relative;
  }
  .main-nav a.is-active { color: var(--royal); }
  .main-nav a.is-active::after {
    content: ""; position: absolute; left: 0; right: 0; bottom: -2px; height: 2px; background: var(--royal);
  }

  .about { display: flex; justify-content: space-between; padding: 46px 74px 0 74px; height: 427px; }
  .about-text { width: 425px; padding-top: 23px; }
  .about-title { font-family: "Lato", sans-serif; font-weight: 900; font-size: 29px; color: var(--navy); margin-bottom: 10px; }
  .about-lead { font-family: "Lato", sans-serif; font-weight: 700; font-size: 15.5px; line-height: 23px; color: var(--royal); margin-bottom: 8px; font-weight: 600; }
  .about-body { font-size: 16px; line-height: 26px; color: var(--body-grey); }
  .about-visual {
    width: 600px; height: 322px;
    background: radial-gradient(ellipse at 75% 30%, #6b625a 0%, #2a2928 45%, #0b0c0e 100%);
  }

  .site-footer {
    position: absolute; left: 0; right: 0; top: 518px; bottom: 0; background: var(--navy);
    text-align: center; color: var(--white);
  }
  .footer-links { margin-top: 34px; font-size: 14px; font-weight: 600; letter-spacing: 0.2px; }
  .footer-links a { color: var(--white); text-decoration: none; text-transform: uppercase; }
  .footer-links .sep { margin: 0 9px; }
  .copyright { margin-top: 8px; font-size: 13.5px; color: var(--copy-blue); }
  .social { margin-top: 12px; display: flex; justify-content: center; gap: 20px; }
  .social a { width: 20px; height: 20px; border-radius: 50%; background: var(--white); display: block; }
</style>
</head>
<body>
  <header class="site-header">
    <a class="brand" href="#">
      <span class="brand-square"></span>
      <span class="brand-name">NORVANE</span>
    </a>
    <nav class="main-nav">
      <a href="#" class="is-active">Home</a>
      <a href="#">About Norvane</a>
      <a href="#">Our Approach &amp; Philosophy</a>
      <a href="#">Contact Us</a>
    </nav>
  </header>

  <main class="about">
    <section class="about-text">
      <h1 class="about-title">ABOUT NORVANE</h1>
      <p class="about-lead">Norvane Investment Management was founded in 2016 with a clear vision to create an independent and nimble firm focused on generating superior risk-adjusted returns.</p>
      <p class="about-body">Norvane has designed an innovative investment approach which aims to harness the best elements of alternative investment management whilst reducing its recognised shortcomings. We are a performance and client focused firm, committed to building lasting relationships, treating our clients like partners rather than revenue streams.</p>
    </section>
    <div class="about-visual" role="img" aria-label="Photo of a businessman drawing a glowing line chart of monthly growth on a dark screen"></div>
  </main>

  <footer class="site-footer">
    <div class="footer-links">
      <a href="#">Disclaimer</a><span class="sep">/</span>
      <a href="#">Terms and Conditions</a><span class="sep">/</span>
      <a href="#">Stewardship</a><span class="sep">/</span>
      <a href="#">Pillar III</a>
    </div>
    <p class="copyright">Copyright © 2017. Company Name. All Right Reserved</p>
    <div class="social">
      <a href="#" aria-label="Social profile 1"></a>
      <a href="#" aria-label="Social profile 2"></a>
      <a href="#" aria-label="Social profile 3"></a>
      <a href="#" aria-label="Social profile 4"></a>
      <a href="#" aria-label="Video channel"></a>
    </div>
  </footer>
</body>
</html>
```